PlayTallyCollective - Game Statistics and Achievement Tracking

I need a new modern design for an existing website.

The website is a project to track statistics and achievements for games (currently Vaporn Achievements/Stats and stats for Cargo Haul Odyssey 2 and Frontier Rig Journeys).
I am currently expanding the site with other platforms (like QVR) and more games.
I am also adding a user registration/signin with user profiles to show off their achievements and stats across all platforms and games.

The current website is available at https://plytly.example/
To search for data you can use the username "pixelornin" (without quotes).

The design should be modern and extendable and contain space for a logo.

The logo should match the project. It should combine Gaming with statistics.

Target Market(s)

Video game players

Number of Pages Required

5+ page

Font styles to use
Sans Serif

Requirements
Must have
• Basic Layout, User profile page (not yet available on live site), Search Page for Platforms/Games, Platform profile page, Dark theme

```html
<!DOCTYPE html>
<html lang="en">
<head>
<meta charset="utf-8">
<title>Game Statistics – Your Gaming Stats Unified</title>
<link rel="stylesheet" href="https://fonts.googleapis.com/css2?family=Lato:wght@400;700&display=swap">
<style>
:root{
  --red:#d90a2c;
  --ink:#1d1d1f;
  --muted:#6b6b70;
  --plum:#231528;
  --plum-deep:#1a0f1f;
  --white:#ffffff;
  --line:#e4e4e8;
}
*{box-sizing:border-box;margin:0;padding:0}
html,body{width:1200px;height:3565px;overflow:hidden}
body{font-family:"Lato",sans-serif;color:var(--ink);background:var(--white);position:relative}
.section{position:absolute;left:0;width:1200px}
.abs{position:absolute}

/* hero */
.hero{top:0;height:616px;background:radial-gradient(ellipse at 50% 40%,#6a5a72 0%,#3d2e47 45%,#21172a 100%)}
.brand{left:93px;top:28px;font-size:30px;color:var(--white)}
.nav{left:450px;top:38px;display:flex;gap:21px;font-size:15px;color:#eee;list-style:none}
.signin{left:994px;top:26px;width:115px;height:43px;background:var(--red);color:var(--white);border-radius:3px;font-size:15px;font-weight:700;display:flex;align-items:center;justify-content:center;gap:10px}
.hero-title{top:198px;width:1200px;text-align:center;font-size:52px;color:var(--white)}
.hero-sub{top:272px;width:1200px;text-align:center;font-size:24px;line-height:38px;color:#f1f1f1}
.search{display:flex;align-items:center;background:var(--white);border:1px solid var(--line);border-radius:3px;padding:0 8px 0 16px}
.search .icon{margin-right:14px}
.search .ph{flex:1;font-size:15px;color:#444}
.btn{background:var(--red);color:var(--white);font-size:15px;font-weight:700;border-radius:3px;display:flex;align-items:center;justify-content:center}
.hero-search{left:270px;top:382px;width:659px;height:58px}
.hero-search .btn{width:123px;height:41px}

/* offer */
.offer{top:616px;height:702px}
.title{width:1200px;text-align:center;font-weight:400}
.offer .title{top:74px;font-size:42px}
.offer .lead{top:132px;width:1200px;text-align:center;font-size:15px;line-height:26px}
.card{top:219px;width:325px;height:400px;background:var(--white);box-shadow:0 2px 10px rgba(0,0,0,.08);border-radius:3px;overflow:hidden}
.card .photo{height:250px}
.card h3{font-size:19px;font-weight:400;margin:14px 17px 8px}
.card p{font-size:13px;color:var(--muted);line-height:19px;margin:0 17px}
.card .more{margin:14px 17px;color:var(--red);font-size:15px;font-weight:700;display:flex;align-items:center;gap:8px}

/* how */
.how{top:1318px;height:492px;background:var(--plum)}
.how .art{left:577px;top:0;width:623px;height:492px;background:linear-gradient(135deg,#2a1732,#3a1840 40%,#1c1a30 75%,#14222e)}
.how .text{left:102px;top:104px;width:420px;color:var(--white)}
.how h2{font-size:22px;font-weight:700;margin-bottom:12px}
.how h4{font-size:17px;font-weight:700;line-height:26px;margin-bottom:12px}
.how p{font-size:14px;line-height:22px;margin-bottom:8px}
.checks{list-style:none}
.checks li{display:flex;align-items:center;gap:10px}
.how .checks li{font-size:15px;line-height:24px}

/* feature */
.feature{top:1810px;height:683px}
.feature .photo{left:95px;top:83px;width:475px;height:517px;background:linear-gradient(160deg,#b9c2c6,#6f7a80 55%,#a4302f)}
.feature .search{left:626px;top:139px;width:465px;height:55px}
.feature .search .btn{width:122px;height:41px}
.feature h2{left:626px;top:218px;width:480px;font-size:33px;font-weight:400;line-height:41px}
.feature p{left:626px;top:306px;width:470px;font-size:13.5px;line-height:22px}
.feature .checks{left:626px;top:407px}
.feature .checks li{font-size:15px;line-height:30px}

/* projects */
.projects{top:2493px;height:649px;background:var(--plum-deep)}
.projects .title{top:48px;font-size:42px;color:var(--white)}
.projects .lead{top:112px;width:1200px;text-align:center;font-size:16px;line-height:26px;color:var(--white)}
.tile{border-radius:2px}

/* footer */
.footer{top:3142px;height:423px}
.footer .title{top:76px;font-size:33px;font-weight:700}
.footer .about{left:240px;top:133px;width:720px;text-align:center;font-size:15px;line-height:22px}
.footer .links{top:210px;width:1200px;display:flex;justify-content:center;font-size:15px;color:#444;list-style:none}
.footer .links li{padding:0 10px;border-left:1px solid #999}
.footer .links li:first-child{border-left:none}
.footer .social{top:256px;width:1200px;display:flex;justify-content:center;gap:16px;font-size:14px;font-weight:700}
.footer .rule{left:93px;top:296px;width:1013px;height:1px;background:#999}
.footer .copy{top:318px;width:1200px;text-align:center;font-size:12px;color:#555}
</style>
</head>
<body>

<header class="section hero" role="img" aria-label="Hero background: dim purple-lit gaming room with a player silhouette">
  <div class="abs brand">Game Statistics</div>
  <ul class="abs nav"><li>Home</li><li>About Us</li><li>Platforms</li><li>Games</li><li>Leaderboards</li></ul>
  <div class="abs signin">Sign In
    <svg width="16" height="16" viewBox="0 0 16 16" fill="none" stroke="#fff" stroke-width="1.6"><path d="M9 2h4v12H9M2 8h8M7 5l3 3-3 3"/></svg>
  </div>
  <h1 class="abs hero-title" style="font-weight:400">Your Gaming Stats Unified.</h1>
  <p class="abs hero-sub">Rack Achievements, Milestones, And Gaming Progress Across<br>Vaporn, QVR, And More!</p>
  <div class="abs search hero-search">
    <svg class="icon" width="20" height="20" viewBox="0 0 20 20" fill="none" stroke="#aaa" stroke-width="1.8"><circle cx="8.5" cy="8.5" r="6"/><path d="M13 13l5 5"/></svg>
    <span class="ph">Search your username or platform...</span>
    <span class="btn">Get Started</span>
  </div>
</header>

<section class="section offer">
  <h2 class="abs title">What We Offer</h2>
  <p class="abs lead">Track Your Achievements, Compare With Friends, And Explore Your Gaming Progress<br>Across Multiple Platforms With Our Comprehensive Services.</p>
  <article class="abs card" style="left:83px">
    <div class="photo" role="img" aria-label="Player at a monitor showing a victory screen" style="background:linear-gradient(135deg,#1b2a5a,#2f4a8a 50%,#0e1424)"></div>
    <h3>Achievement Tracking &amp; Stats</h3>
    <p>Users Can Link Their Gaming Accounts (Vaporn, QVR, Hexbox, Etc.) To Track Their Achievements, Compare Stats...</p>
    <div class="more">read more <svg width="12" height="12" viewBox="0 0 12 12" fill="none" stroke="#d90a2c" stroke-width="1.6"><path d="M2 2l4 4-4 4M6 2l4 4-4 4"/></svg></div>
  </article>
  <article class="abs card" style="left:437px">
    <div class="photo" role="img" aria-label="Glowing glass cubes scattering coloured light" style="background:radial-gradient(circle at 50% 50%,#6a6a30,#2a2f24 45%,#121410)"></div>
    <h3>Achievement Tracking &amp; Stats</h3>
    <p>Users Can Link Their Gaming Accounts (Vaporn, QVR, Hexbox, Etc.) To Track Their Achievements, Compare Stats...</p>
    <div class="more">read more <svg width="12" height="12" viewBox="0 0 12 12" fill="none" stroke="#d90a2c" stroke-width="1.6"><path d="M2 2l4 4-4 4M6 2l4 4-4 4"/></svg></div>
  </article>
  <article class="abs card" style="left:792px">
    <div class="photo" role="img" aria-label="Player with headphones celebrating in front of a bright monitor" style="background:linear-gradient(135deg,#dfe4ea,#a9b6c4 55%,#3a3f4a)"></div>
    <h3>Achievement Tracking &amp; Stats</h3>
    <p>Users Can Link Their Gaming Accounts (Vaporn, QVR, Hexbox, Etc.) To Track Their Achievements, Compare Stats...</p>
    <div class="more">read more <svg width="12" height="12" viewBox="0 0 12 12" fill="none" stroke="#d90a2c" stroke-width="1.6"><path d="M2 2l4 4-4 4M6 2l4 4-4 4"/></svg></div>
  </article>
</section>

<section class="section how">
  <div class="abs text">
    <h2>How It Works</h2>
    <h4>Easily Connect Your Gaming Accounts, Track Your Progress, And Explore Detailed Stats And Achievements!</h4>
    <p>Get Started By Creating An Account And Linking Your Gaming Profiles. Track Your Achievements And Explore Detailed Stats Across Popular Platforms Like Vaporn, QVR, And Hexbox.</p>
    <ul class="checks">
      <li><svg width="14" height="14" viewBox="0 0 14 14" fill="none" stroke="#d90a2c" stroke-width="2"><path d="M2 7l3.5 3.5L12 3"/></svg>create an account or sign in</li>
      <li><svg width="14" height="14" viewBox="0 0 14 14" fill="none" stroke="#d90a2c" stroke-width="2"><path d="M2 7l3.5 3.5L12 3"/></svg>connect your gaming accounts</li>
      <li><svg width="14" height="14" viewBox="0 0 14 14" fill="none" stroke="#d90a2c" stroke-width="2"><path d="M2 7l3.5 3.5L12 3"/></svg>track achievements and stats</li>
      <li><svg width="14" height="14" viewBox="0 0 14 14" fill="none" stroke="#d90a2c" stroke-width="2"><path d="M2 7l3.5 3.5L12 3"/></svg>join the community</li>
    </ul>
  </div>
  <div class="abs art" role="img" aria-label="Illustration of a neon pink and teal game dashboard interface"></div>
</section>

<section class="section feature">
  <div class="abs photo" role="img" aria-label="Hands holding a game controller with a phone mounted on it"></div>
  <div class="abs search">
    <svg class="icon" width="20" height="20" viewBox="0 0 20 20" fill="none" stroke="#222" stroke-width="2"><circle cx="8.5" cy="8.5" r="6"/><path d="M13 13l5 5"/></svg>
    <span class="ph" style="color:#222">Search your username or platform...</span>
    <span class="btn">Get Started</span>
  </div>
  <h2 class="abs">As Opposed To Using Content Here, Content Here Making</h2>
  <p class="abs">Less Normal Distribution Of Letters, As Opposed To Using 'Content Here, Content Here', Making It Look Like Readable English. Many Desktop Publishing Packages And Web Page Editors Now Use Lorem Ipsum As Their Default Model Text, And A Search</p>
  <ul class="abs checks">
    <li><svg width="14" height="14" viewBox="0 0 14 14" fill="none" stroke="#d90a2c" stroke-width="2"><path d="M2 7l3.5 3.5L12 3"/></svg>lorem ipsum is that it has a more</li>
    <li><svg width="14" height="14" viewBox="0 0 14 14" fill="none" stroke="#d90a2c" stroke-width="2"><path d="M2 7l3.5 3.5L12 3"/></svg>lorem ipsum is that it has a more</li>
    <li><svg width="14" height="14" viewBox="0 0 14 14" fill="none" stroke="#d90a2c" stroke-width="2"><path d="M2 7l3.5 3.5L12 3"/></svg>lorem ipsum is that it has a more</li>
    <li><svg width="14" height="14" viewBox="0 0 14 14" fill="none" stroke="#d90a2c" stroke-width="2"><path d="M2 7l3.5 3.5L12 3"/></svg>lorem ipsum is that it has a more</li>
  </ul>
</section>

<section class="section projects">
  <h2 class="abs title">Our Recent Projects</h2>
  <p class="abs lead">Lorem Ipsum as their default model text, and a search for 'lorem<br>ipsum' will uncover many infancy.</p>
  <div class="abs tile" role="img" aria-label="Office with rows of gaming desks" style="left:112px;top:192px;width:318px;height:184px;background:linear-gradient(135deg,#5a4a40,#2a2a2e)"></div>
  <div class="abs tile" role="img" aria-label="Player at a screen lit in blue and orange" style="left:453px;top:192px;width:318px;height:184px;background:linear-gradient(90deg,#0f3a52,#1f5a7a 45%,#8a4a2a)"></div>
  <div class="abs tile" role="img" aria-label="Gaming studio room with posters on the wall" style="left:793px;top:192px;width:293px;height:184px;background:linear-gradient(135deg,#9aa0a8,#4a4e58)"></div>
  <div class="abs tile" role="img" aria-label="Laptop showing a colourful game" style="left:112px;top:405px;width:205px;height:185px;background:linear-gradient(135deg,#1a2a4a,#3a3a6a 55%,#101018)"></div>
  <div class="abs tile" role="img" aria-label="Players at desks in a red-lit gaming room" style="left:339px;top:405px;width:335px;height:185px;background:linear-gradient(135deg,#2a1818,#4a2a2a 50%,#1a1a1a)"></div>
  <div class="abs tile" role="img" aria-label="Hands holding a dark game controller" style="left:696px;top:405px;width:390px;height:185px;background:linear-gradient(135deg,#1a1a1c,#3a3a3e 60%,#1e1e20)"></div>
</section>

<footer class="section footer">
  <h2 class="abs title">Game Statistics</h2>
  <p class="abs about">lorem ipsum is that it has a more-or-less normal distribution of letters, as opposed to using 'content here, content here', making it look like readable english. many desktop publishing packages and web page editors now use lorem ipsum as their default model text, and a search for</p>
  <ul class="abs links"><li>Home</li><li>About Us</li><li>Platforms</li><li>Games</li><li>Leaderboards</li></ul>
  <div class="abs social"><span>Linkory</span><span>Friendly</span><span>Snapora</span></div>
  <div class="abs rule"></div>
  <p class="abs copy">© 2024 PlayTallyCollective</p>
</footer>

</body>
</html>
```